New Web Design Project

Number of Pages Required

1 page

Requirements
Must have
• An Overview / Background of the Business & Services(not for profit rescue animal farm)
• The Target Market / Audience you are trying to reach (animal lovers)
• Design Specifics; any preferences or ideas for Style, Colour, Imagery, etc (no preferences)

```html
<!DOCTYPE html>
<html lang="en">
<head>
<meta charset="utf-8">
<title>Cedar Hollow Farms</title>
<link href="https://fonts.googleapis.com/css2?family=Poppins:wght@400;500&family=Open+Sans:wght@400;600&family=Roboto+Condensed:wght@400&display=swap" rel="stylesheet">
<style>
:root{
  --green:#2f6b1d;
  --green-dark:#1d4a10;
  --green-light:#4f8f2c;
  --blue:#1f4f86;
  --blue-dark:#163a63;
  --ink:#222;
  --text:#444;
  --muted:#777;
  --footer:#141414;
  --white:#fff;
}
*{margin:0;padding:0;box-sizing:border-box}
html,body{width:1200px;height:4433px;overflow:hidden;background:var(--white)}
body{position:relative;font-family:"Open Sans",sans-serif;color:var(--text)}
h1,h2,h3,h4{font-weight:400}
.abs{position:absolute}
.header .brand{left:50px;top:26px;width:230px;text-align:center}
.brand-mark{width:40px;height:40px;border-radius:50%;background:var(--green);margin:0 auto 8px}
.brand-name{font-family:"Poppins",sans-serif;font-weight:500;font-size:18px;color:var(--ink);white-space:nowrap}
.phone{left:730px;top:40px;font-size:19px;color:var(--ink);display:flex;align-items:center;gap:8px}
.search{left:912px;top:38px;width:200px;height:32px;border:1.5px solid #555;border-radius:16px;font-size:13px;padding:6px 14px;color:#555}
.search svg{position:absolute;right:12px;top:8px}
.nav{left:478px;top:94px;display:flex;gap:40px;font-size:18px;color:var(--ink)}
.nav .active{color:var(--green-light)}
.hero{left:0;top:152px;width:1200px;height:640px;background:linear-gradient(180deg,#6fa8e0 0%,#b9d7ef 38%,#e9ece4 50%,#8dbb4f 66%,#3e7a1d 100%)}
.hero-curve{left:0;top:650px}
.hero-title{left:148px;top:305px;font-family:"Roboto Condensed",sans-serif;font-weight:400;font-size:84px;color:var(--green);line-height:1}
.hero-sub{left:148px;top:405px;font-family:"Roboto Condensed",sans-serif;font-size:38px;color:var(--ink)}
.arrow{width:22px;height:22px;border-radius:50%;background:rgba(40,40,40,.7);top:420px}
.section-title{width:1200px;left:0;text-align:center;font-family:"Poppins",sans-serif;font-weight:400;font-size:44px;color:var(--ink)}
.service{width:300px;text-align:center}
.service .photo{width:190px;height:190px;border-radius:50%;margin:0 auto 30px;border:4px solid #ddd}
.service h3{font-family:"Poppins",sans-serif;font-size:23px;color:var(--ink);margin-bottom:10px}
.service p{font-size:15px;line-height:1.6;color:var(--text);width:230px;margin:0 auto}
.about{left:0;top:1290px;width:1200px;height:595px}
.about-title{color:var(--white)}
.about-text{left:210px;top:1508px;width:780px;text-align:center;color:var(--white);font-size:14.5px;line-height:1.75}
.video{left:245px;top:1655px;width:710px;height:400px;border:4px solid #fff;box-shadow:0 10px 24px rgba(0,0,0,.35);background:linear-gradient(180deg,#1f3f16 0%,#2e5a22 40%,#5f9a35 65%,#86c24c 100%)}
.play{left:565px;top:1812px;width:70px;height:70px;border-radius:50%;background:rgba(0,0,0,.55);border:3px solid rgba(255,255,255,.8)}
.card{width:474px;height:475px;background:var(--white);box-shadow:0 2px 12px rgba(0,0,0,.25);text-align:center;top:2295px}
.card .photo{height:260px}
.card h3{font-family:"Poppins",sans-serif;font-size:24px;color:var(--ink);margin:22px 0 12px}
.card p{font-size:15px;line-height:1.65;width:360px;margin:0 auto 12px}
.btn{display:inline-block;background:var(--green);color:var(--white);border-radius:20px;font-size:15px;padding:7px 32px}
.testimonial{left:0;top:2870px;width:1200px;height:600px}
.quote{left:120px;top:3035px;font-family:"Poppins",sans-serif;font-size:110px;color:var(--green-light);line-height:1}
.t-title{left:120px;top:3098px;font-family:"Poppins",sans-serif;font-weight:400;font-size:44px;color:var(--white)}
.t-text{left:122px;top:3168px;width:540px;color:var(--white);font-size:14.5px;line-height:1.9}
.t-name{left:122px;top:3302px;color:var(--white);font-size:19px;font-weight:600}
.t-stars{left:122px;top:3340px;display:flex;gap:6px}
.person{left:680px;top:2960px;width:400px;height:510px;background:radial-gradient(ellipse at 50% 30%,rgba(214,180,150,.55) 0%,rgba(60,80,110,.6) 35%,rgba(30,42,62,.0) 75%)}
.footer-bg{left:0;top:3930px;width:1200px;height:503px}
.contact-box{left:135px;top:3690px;width:935px;height:385px;background:var(--white);box-shadow:0 2px 10px rgba(0,0,0,.25);display:flex}
.contact-form{width:448px;padding:30px 55px}
.contact-form h3{font-family:"Poppins",sans-serif;font-size:24px;color:var(--ink);margin-bottom:12px}
.field{border:1px solid #bbb;height:38px;font-size:13px;padding:9px 10px;color:#444;margin-bottom:9px;width:325px}
.field.msg{height:78px}
.send{background:var(--green);color:var(--white);border-radius:18px;font-size:15px;width:98px;text-align:center;padding:6px 0;margin-top:4px}
.map{flex:1;background:linear-gradient(135deg,#e6e6e6,#cfcfcf)}
.f-col{top:4128px;color:#ddd;font-size:14px}
.f-col h4{font-size:16px;color:#eee;margin-bottom:18px;letter-spacing:.3px}
.f-list li{list-style:none;margin-bottom:5px;font-size:13px;line-height:18px}
.f-list li::before{content:"» ";}
.f-contact div{display:flex;gap:14px;align-items:flex-start;margin-bottom:10px;font-size:13px;line-height:1.3}
.f-icon{width:22px;height:22px;border-radius:50%;border:1.5px solid #ddd;flex:none}
.mail{left:845px;top:4195px;width:218px;height:44px;border:1.5px solid #ddd;border-radius:22px;color:#bbb;font-size:13px;padding:12px 18px}
.mail span{position:absolute;right:14px;top:12px;width:18px;height:18px;border-radius:50%;background:#ddd}
.f-line{left:95px;top:4333px;width:1010px;height:1px;background:#444}
.copy{left:0;top:4368px;width:1200px;text-align:center;color:#ddd;font-size:13px}
</style>
</head>
<body>

<header class="header">
  <div class="abs brand"><div class="brand-mark"></div><div class="brand-name">Cedar Hollow Farms</div></div>
  <div class="abs phone">
    <svg width="22" height="22" viewBox="0 0 24 24"><path d="M6.6 10.8a15 15 0 0 0 6.6 6.6l2.2-2.2c.3-.3.7-.4 1-.2 1.1.4 2.3.6 3.6.6.6 0 1 .4 1 1V20c0 .6-.4 1-1 1A17 17 0 0 1 3 4c0-.6.4-1 1-1h3.5c.6 0 1 .4 1 1 0 1.3.2 2.5.6 3.6.1.3 0 .7-.2 1z" fill="#2a5ea8"/></svg>
    888-555-0142
  </div>
  <div class="abs search">Search
    <svg width="14" height="14" viewBox="0 0 14 14"><circle cx="6" cy="6" r="4.5" fill="none" stroke="#333" stroke-width="2"/><path d="M9.5 9.5l3.5 3.5" stroke="#333" stroke-width="2"/></svg>
  </div>
  <nav class="abs nav"><span class="active">Home</span><span>About us</span><span>Services</span><span>Farms</span><span>Blog</span><span>Contact us</span></nav>
</header>

<section>
  <div class="abs hero" role="img" aria-label="Lambs standing in a green meadow under a blue sky"></div>
  <svg class="abs hero-curve" width="1200" height="145" viewBox="0 0 1200 145">
    <path d="M0 50 Q600 130 1200 50 L1200 145 L0 145Z" fill="#fff"/>
    <path d="M200 100 Q600 30 1000 100" fill="none" stroke="#1f4f86" stroke-width="5"/>
  </svg>
  <h1 class="abs hero-title">Cedar Hollow Farms</h1>
  <p class="abs hero-sub">We are a not for profit rescue animal farm</p>
  <div class="abs arrow" style="left:68px"></div>
  <div class="abs arrow" style="left:1102px"></div>
</section>

<section>
  <h2 class="abs section-title" style="top:795px">Our Services</h2>
  <div class="abs service" style="left:113px;top:922px"><div class="photo" role="img" aria-label="Volunteer feeding cows" style="background:radial-gradient(circle at 50% 40%,#d9c6a4,#7a6a54 60%,#4d5a3a)"></div><h3>Rescue animal</h3><p>The point of using Lorem Ipsum is that it has a more-or-less normal</p></div>
  <div class="abs service" style="left:450px;top:922px"><div class="photo" role="img" aria-label="Girl caring for a horse" style="background:radial-gradient(circle at 50% 45%,#c9a07a,#8c6a4a 55%,#6f8fb0)"></div><h3>Caring animals</h3><p>The point of using Lorem Ipsum is that it has a more-or-less</p></div>
  <div class="abs service" style="left:785px;top:922px"><div class="photo" role="img" aria-label="Goats in a sanctuary barn" style="background:radial-gradient(circle at 50% 50%,#e4dccb,#a88a66 55%,#5e4630)"></div><h3>Animal sanctuary</h3><p>The point of using Lorem Ipsum is that it has a more-or-less</p></div>
</section>

<section>
  <svg class="abs about" width="1200" height="595" viewBox="0 0 1200 595">
    <defs><linearGradient id="greenBand" x1="0" y1="0" x2="0" y2="1"><stop offset="0" stop-color="#2f6b1d"/><stop offset="1" stop-color="#1d4a10"/></linearGradient></defs>
    <path d="M0 0 Q600 90 1200 0 L1200 595 L0 595Z" fill="url(#greenBand)"/>
  </svg>
  <h2 class="abs section-title about-title" style="top:1435px">About us</h2>
  <p class="abs about-text">It is a long established fact that a reader will be distracted by the readable content of a page when looking at its layout. The point of using Lorem Ipsum is that it has a more-or-less normal distribution of letters, as opposed to using 'Content here, content here', making it look like readable English. Many desktop publishing packages and web page editors now use Lorem Ipsum as their default model text.</p>
  <div class="abs video" role="img" aria-label="Video still of sheep grazing in a forest clearing"></div>
  <div class="abs play"><svg width="64" height="64" viewBox="0 0 64 64"><path d="M26 20 L44 32 L26 44Z" fill="#fff"/></svg></div>
</section>

<section>
  <h2 class="abs section-title" style="top:2175px">Our Features</h2>
  <article class="abs card" style="left:103px">
    <div class="photo" role="img" aria-label="Herd of cattle grazing in a field" style="background:linear-gradient(180deg,#7aa84a,#5f8f3a 50%,#3f6e22)"></div>
    <h3>Neque porro quisquam</h3>
    <p>The point of using Lorem Ipsum is that it has a more-or-less normal distribution of letters, as opposed to using 'Content here.</p>
    <span class="btn">View More</span>
  </article>
  <article class="abs card" style="left:622px">
    <div class="photo" role="img" aria-label="Horses grazing in a pasture" style="background:linear-gradient(180deg,#4e6f8c 0%,#7a8a5a 35%,#6f8f4a 55%,#4c7a2a 100%)"></div>
    <h3>Dolorem ipsum quia dolor</h3>
    <p>The point of using Lorem Ipsum is that it has a more-or-less normal distribution of letters, as opposed to using 'Content here.</p>
    <span class="btn">View More</span>
  </article>
</section>

<section>
  <svg class="abs testimonial" width="1200" height="600" viewBox="0 0 1200 600">
    <defs><linearGradient id="blueBand" x1="0" y1="0" x2="1" y2="0"><stop offset="0" stop-color="#163a63"/><stop offset="1" stop-color="#2a5f96"/></linearGradient></defs>
    <path d="M0 75 Q600 -40 1200 75 L1200 600 L0 600Z" fill="url(#blueBand)"/>
  </svg>
  <div class="abs quote">“</div>
  <h2 class="abs t-title">Testimonial</h2>
  <p class="abs t-text">"It is a long established fact that a reader will be distracted by the readable content of a page when looking at its layout. The point of using Lorem Ipsum is that it has a more-or-less normal distribution of letters, as use will uncover many web sites still in their infancy."</p>
  <div class="abs t-name">Daniel Reed</div>
  <div class="abs t-stars">
    <svg width="170" height="26" viewBox="0 0 170 26" fill="#fff">
      <path id="star" d="M13 1l3.5 7.6 8.3.9-6.2 5.6 1.8 8.2L13 19l-7.4 4.3 1.8-8.2L1.2 9.5l8.3-.9z"/>
      <use href="#star" x="34"/><use href="#star" x="68"/><use href="#star" x="102"/><use href="#star" x="136"/>
    </svg>
  </div>
  <div class="abs person" role="img" aria-label="Smiling farm volunteer holding a clipboard and giving a thumbs up"></div>
</section>

<section>
  <h2 class="abs section-title" style="top:3570px">Contact us</h2>
  <svg class="abs footer-bg" width="1200" height="503" viewBox="0 0 1200 503">
    <path d="M0 60 Q600 -40 1200 60 L1200 503 L0 503Z" fill="#141414"/>
  </svg>
  <div class="abs contact-box">
    <form class="contact-form">
      <h3>Quick Contact</h3>
      <div class="field">Name</div>
      <div class="field">Phone number</div>
      <div class="field">Email address</div>
      <div class="field msg">Message</div>
      <div class="send">SEND</div>
    </form>
    <div class="map" role="img" aria-label="Street map showing the farm location">
      <svg width="487" height="385" viewBox="0 0 487 385"><path d="M243 160c-14 0-24 10-24 24 0 18 24 42 24 42s24-24 24-42c0-14-10-24-24-24z" fill="#e0403a"/><circle cx="243" cy="184" r="8" fill="#fff"/></svg>
    </div>
  </div>
</section>

<footer>
  <div class="abs f-col" style="left:160px">
    <h4>INFORMATION</h4>
    <ul class="f-list"><li>Privacy Policy</li><li>Animal farm</li><li>Rescue</li><li>Contact</li></ul>
  </div>
  <div class="abs f-col f-contact" style="left:452px">
    <h4>CONTACT US</h4>
    <div><span class="f-icon"></span><span>Brook Lane Services, Inc.<br>412 Meadow Road, Fairview WA 99000</span></div>
    <div><span class="f-icon"></span><span>509-555-0187</span></div>
    <div><span class="f-icon"></span><span>hello@cedarhollow.org</span></div>
  </div>
  <div class="abs f-col" style="left:845px"><h4>JOIN OUR MAILING LIST</h4></div>
  <div class="abs mail">Email address<span></span></div>
  <div class="abs f-line"></div>
  <p class="abs copy">Copyright © 2019. All Rights Reserved</p>
</footer>

</body>
</html>
```